Quintel Packaging Business Card

Project Overview
We are seeking a modern, minimalist business card that effectively represents our company while making a bold and lasting impression. The design should reflect trust, professionalism, and innovation, reinforcing our expertise in custom plastic manufacturing for warehouse and distribution centers.

Provided Assets & Specifications
Logo: We will provide our official logo for integration into the design.
Design Files: Photoshop (PSD) files for our printing specifications will be supplied.

Card Size & Material:
Dimensions: 3.5" x 2"
Material: 1/8" Radius Plastic Business Cards with 1/8" Rounded Corners
Clear plastic background—the design should strategically incorporate transparency.
Orientation: The card should be designed in landscape format for a sleek and professional presentation.

Design Requirements:
Logo Prominence
The logo must be the focal point of the card.
Space should be used effectively to draw attention to the logo while maintaining a minimalist layout.

Clear Plastic Integration
The transparent background should create the illusion of blank space, enhancing the modern and high-quality feel.
Avoid any frosted effects—we do not want white areas to appear semi-transparent.

Minimalist & Impactful
Clean, structured, and easy to read at a glance.
Focus on sharp contrast to ensure legibility and visibility.
The design should instill confidence and reflect our role as a leading plastics manufacturer.

Color Palette & Contrast
Primary Colors: Blue, Black, White, and Grey
Use bold black or blue for text and key elements to ensure they stand out against the clear plastic.
Avoid light, pastel, or neon colors that may fade into the plastic background.
No frosted or semi-transparent white—we do not want a cloudy effect.

Typography & Information Hierarchy
Bold, modern typography—clear, professional, and highly legible.
The business card should highlight:
Company Logo (Primary Focus)
Full Name & Title
Phone Number
Email
Website

Brand Representation
The card should reflect our expertise in manufacturing high-quality custom plastics for large-scale packaging and distribution businesses.
Our clients rely on us to enhance their brand presence through custom plastic solutions, and our business cards should reinforce that sense of precision and trust.

Final Considerations
Utilize the clear plastic effectively to differentiate our brand from standard business cards.
Maintain a sleek, professional aesthetic while ensuring all text and elements remain legible.
The design should align with our industry, conveying reliability and innovation.
We look forward to seeing a design that captures our brand identity, maximizes the clear plastic medium, and makes a strong, professional impact on our clients.

```html
<!DOCTYPE html>
<html lang="en">
<head>
<meta charset="utf-8">
<title>Quintel Packaging Business Card</title>
<link rel="stylesheet" href="https://fonts.googleapis.com/css2?family=Montserrat:wght@400;500;700&display=swap">
<style>
  :root {
    --backdrop: #1d1d1d;
    --card-white: #ffffff;
    --brand-blue: #028bc0;
    --ink-dark: #343434;
    --ink-black: #1a1a1a;
  }
  * { margin: 0; padding: 0; box-sizing: border-box; }
  html, body {
    width: 1200px;
    height: 1059px;
    overflow: hidden;
    background: var(--backdrop);
    font-family: "Montserrat", sans-serif;
  }
  .business-card {
    position: absolute;
    left: 190px;
    top: 296px;
    width: 820px;
    height: 468px;
    border-radius: 24px;
    background: var(--card-white);
    overflow: hidden;
  }
  .brand-lockup {
    position: absolute;
    left: 39px;
    top: 52px;
    display: flex;
    align-items: center;
    gap: 18px;
  }
  .brand-square {
    width: 60px;
    height: 60px;
    background: var(--brand-blue);
    flex: none;
  }
  .brand-name {
    font-weight: 700;
    font-size: 34px;
    line-height: 1.08;
    letter-spacing: 0.5px;
    color: var(--ink-dark);
  }
  .person {
    position: absolute;
    right: 37px;
    top: 50px;
    text-align: right;
  }
  .person-name {
    font-weight: 700;
    font-size: 40px;
    line-height: 1;
    letter-spacing: 0.5px;
    color: var(--brand-blue);
    white-space: nowrap;
  }
  .person-title {
    margin-top: 9px;
    font-weight: 500;
    font-size: 22px;
    color: var(--ink-black);
  }
  .accent-bar {
    position: absolute;
    right: 0;
    top: 54px;
    width: 12px;
    height: 66px;
    background: var(--brand-blue);
  }
  .contact-band {
    position: absolute;
    left: 0;
    bottom: 0;
    width: 100%;
    height: 201px;
    background: var(--brand-blue);
    color: var(--card-white);
  }
  .address {
    position: absolute;
    left: 39px;
    top: 2px;
    font-size: 22px;
    line-height: 33px;
  }
  .contact-list {
    position: absolute;
    left: 39px;
    top: 84px;
    list-style: none;
    font-size: 22px;
  }
  .contact-list li {
    display: flex;
    align-items: center;
    height: 32.5px;
  }
  .contact-icon {
    width: 19px;
    height: 19px;
    margin-right: 9px;
    fill: var(--card-white);
  }
  .band-mark {
    position: absolute;
    left: 623px;
    top: 28px;
    width: 150px;
    height: 150px;
    background: var(--card-white);
    border-radius: 14px;
  }
</style>
</head>
<body>
  <main class="business-card">
    <div class="brand-lockup">
      <span class="brand-square"></span>
      <span class="brand-name">Quintel<br>Packaging</span>
    </div>

    <div class="person">
      <p class="person-name">MARCUS ELLERY</p>
      <p class="person-title">Managing Director</p>
    </div>
    <span class="accent-bar"></span>

    <section class="contact-band">
      <p class="address">Your address, City<br>State, Zip 1234</p>
      <ul class="contact-list">
        <li>
          <svg class="contact-icon" viewBox="0 0 24 24" aria-hidden="true">
            <path d="M2 9c0-3 5-5 10-5s10 2 10 5v2h-5V8.5c-1.5-.6-3.300-.9-5-.9s-3.500.3-5 .9V11H2z"/>
            <path d="M6 11l2-2h8l2 2 2 9H4z"/>
          </svg>
          123 456 789
        </li>
        <li>
          <svg class="contact-icon" viewBox="0 0 24 24" aria-hidden="true">
            <path d="M2 6h20v1.2l-10 6.3L2 7.2z"/>
            <path d="M2 9.4l10 6.3 10-6.3V18H2z"/>
          </svg>
          info@quintelpack.com
        </li>
        <li>
          <svg class="contact-icon" viewBox="0 0 24 24" aria-hidden="true">
            <path d="M12 2a10 10 0 1 0 0 20 10 10 0 0 0 0-20zm-1 3.5c1 .8.4 2-.6 2.5-1 .6-.2 1.800.9 1.800 1.500 0 1.600 2 .3 2.600-1.400.7-2.600-.5-3.800-.2-1 .3-1.400 1.600-2.500 1.200A7.500 7.500 0 0 1 11 5.500zm2.500 14.200c-.6-1.300.2-2.600 1.400-3.200 1.400-.7 2.800-.1 4.200-1.100a7.500 7.500 0 0 1-5.600 4.300z"/>
          </svg>
          www.quintelpack.com
        </li>
      </ul>
      <span class="band-mark"></span>
    </section>
  </main>
</body>
</html>
```